I need a business card design for a new business based in South West Australia.
I specialize in residential window cleaning & general handyman maintenance.

Dale Marsh - 412 SILVER HAWK DETAILING
- Window Cleaning
- House Maintenance

```html
<!DOCTYPE html>
<html lang="en">
<head>
<meta charset="utf-8">
<title>Silver Hawk Detailing – Business Card</title>
<link rel="stylesheet" href="https://fonts.googleapis.com/css2?family=Source+Sans+3:wght@400;600;700;800&display=swap">
<style>
  :root {
    --stage: #000000;
    --card-light: #f3f3f3;
    --brand-blue: #0e4a8a;
    --brand-blue-deep: #0b4680;
    --brand-orange: #f26a10;
    --ink: #3a3a3a;
    --white: #ffffff;
  }
  * { margin: 0; padding: 0; box-sizing: border-box; }
  html, body {
    width: 1200px; height: 900px; overflow: hidden;
    background: var(--stage);
    font-family: "Source Sans 3", "Helvetica Neue", Arial, sans-serif;
  }
  .canvas { position: relative; width: 1200px; height: 900px; }

  .card { position: absolute; top: 200px; width: 310px; height: 502px; overflow: hidden; }
  .card--front {
    left: 265px; background: var(--card-light);
    border-radius: 62px 0 62px 0;
  }
  .card--back {
    left: 641px; background: var(--brand-blue-deep);
    border-radius: 0 62px 0 62px;
  }

  .brand { position: absolute; left: 0; right: 0; text-align: center; }
  .card--front .brand { top: 108px; }
  .brand__name {
    display: inline-flex; align-items: center; gap: 8px;
    font-weight: 800; font-size: 27px; letter-spacing: 0.2px;
    color: var(--brand-blue); line-height: 1;
  }
  .brand__mark { width: 14px; height: 14px; background: var(--brand-blue); display: inline-block; }
  .brand__tagline {
    margin-top: 6px; font-weight: 700; font-size: 11.5px; letter-spacing: 0.4px;
    color: var(--brand-orange);
  }

  .contact { position: absolute; left: 27px; top: 326px; color: var(--ink); }
  .contact__name { font-weight: 600; font-size: 19px; color: var(--brand-blue); line-height: 1; }
  .contact__role { margin-top: 8px; font-size: 14.5px; }
  .contact__address { margin-top: 18px; font-size: 14px; line-height: 15px; }
  .contact__list { list-style: none; margin-top: 11px; font-size: 14px; }
  .contact__list li { display: flex; align-items: center; gap: 6px; height: 19px; }
  .contact__list svg { width: 10px; height: 10px; fill: var(--brand-blue); }

  .back-decor {
    position: absolute; left: 0; top: 0; width: 232px; height: 408px;
    background: linear-gradient(160deg, #0f4e90 0%, #0b4680 70%);
    border-radius: 0 0 12px 0;
  }
  .card--back .brand { top: 427px; }
  .card--back .brand__name { color: var(--white); font-size: 25px; }
  .card--back .brand__tagline { color: var(--white); font-size: 10.5px; margin-top: 5px; }
</style>
</head>
<body>
<main class="canvas">
  <section class="card card--front" aria-label="Card front">
    <div class="brand">
      <div class="brand__name"><span class="brand__mark"></span>SILVER HAWK DETAILING</div>
      <div class="brand__tagline">WINDOW CLEANING &amp; HOUSE MAINTENANCE</div>
    </div>
    <div class="contact">
      <div class="contact__name">DALE MARSH</div>
      <div class="contact__role">Managing Director</div>
      <div class="contact__address">58 Harbour Road<br>Bunbury WA, 6230</div>
      <ul class="contact__list">
        <li><svg viewBox="0 0 10 10" aria-hidden="true"><path d="M1 3c0-1 1-2 4-2s4 1 4 2v1H7V3H3v1H1zM2 5h6l1 4H1z"/></svg>08 9721 5540</li>
        <li><svg viewBox="0 0 10 10" aria-hidden="true"><path d="M0 2h10v6H0zM0.8 2.6L5 5.6l4.2-3v0.9L5 6.5 0.8 3.5z" fill-rule="evenodd"/></svg>hello@silverhawk.au</li>
      </ul>
    </div>
  </section>

  <section class="card card--back" aria-label="Card back">
    <div class="back-decor" role="img" aria-label="Faint embossed brand symbol decoration"></div>
    <div class="brand">
      <div class="brand__name">SILVER HAWK DETAILING</div>
      <div class="brand__tagline">WINDOW CLEANING &amp; HOUSE MAINTENANCE</div>
    </div>
  </section>
</main>
</body>
</html>
```